Business Card design for law firm = Brightvale Australia

We are seeking a new design for our business cards.
We are keeping our logo, which is attached.
We need space for
Name
Title
Address is , which is
Level 7
214 Marlowe Street
Sydney NSW 2047
Phone :
Mobile :
Fax :
Email :
DX :
website www.brightvale-example.com.au

Industry/Entity Type

Law Firm / Banking and Finance

Contact Information for Business Card

We are seeking a new design for our business cards. We are keeping our logo. We need space for Name Title Address is Level 7 214 Marlowe Street Sydney NSW 2047 Phone Mobile Fax Email DX website www.brightvale-example.com.au

Colors
0054AA
0677BA
7BADD7
CADEEF
E8F1F8

Requirements
Must have
• see our website for general feel www.brightvale-example.com.au

```html
<!DOCTYPE html>
<html lang="en">
<head>
<meta charset="utf-8">
<title>Brightvale Australia – Business Card</title>
<link rel="stylesheet" href="https://fonts.googleapis.com/css2?family=Nunito+Sans:wght@400;700&display=swap">
<style>
  :root {
    --backdrop: #ababab;
    --card: #f2f7fa;
    --navy: #1a56a0;
    --cyan: #1a9bc4;
    --mark: #0a99bf;
    --body: #444a50;
    --ghost: rgba(255, 255, 255, 0.85);
  }
  * { margin: 0; padding: 0; box-sizing: border-box; }
  html, body {
    width: 1200px; height: 1000px; overflow: hidden;
    background: var(--backdrop);
    font-family: "Nunito Sans", Arial, sans-serif;
  }
  .canvas { position: relative; width: 1200px; height: 1000px; }
  .card {
    position: absolute; width: 514px; height: 296px;
    background: var(--card); overflow: hidden;
  }
  .card--front { left: 54px; top: 481px; }
  .card--back { left: 623px; top: 265px; }

  .brand {
    position: absolute; left: 0; right: 0; top: 86px;
    display: flex; flex-direction: column; align-items: center;
  }
  .brand__square { width: 56px; height: 56px; background: var(--mark); }
  .brand__name {
    margin-top: 10px; font-size: 32px; font-weight: 400;
    color: var(--navy); line-height: 1; letter-spacing: 0.2px;
  }
  .brand__tagline {
    margin-top: 8px; font-size: 13px; color: var(--cyan); letter-spacing: 0.6px;
  }

  .ghost-name {
    position: absolute; left: 30px; top: -24px;
    font-size: 112px; font-weight: 700; line-height: 1;
    color: var(--ghost); letter-spacing: -2px; white-space: nowrap;
  }
  .person {
    position: absolute; right: 287px; top: 138px; text-align: right;
  }
  .person__name { font-size: 15px; font-weight: 700; color: var(--navy); letter-spacing: 0.3px; }
  .person__title { font-size: 12px; color: var(--cyan); margin-top: 0; letter-spacing: 0.3px; }
  .contact {
    position: absolute; left: 256px; top: 138px;
    font-size: 11.5px; color: var(--body); line-height: 15px; letter-spacing: 0.2px;
  }
  .contact p + p { margin-top: 14px; }
</style>
</head>
<body>
<main class="canvas">
  <section class="card card--front" aria-label="Card front">
    <div class="brand">
      <div class="brand__square"></div>
      <div class="brand__name">Brightvale</div>
      <div class="brand__tagline">strategic legal outsourcing</div>
    </div>
  </section>

  <section class="card card--back" aria-label="Card back">
    <div class="ghost-name" aria-hidden="true">Brightvale</div>
    <div class="person">
      <div class="person__name">Helena Markovic</div>
      <div class="person__title">Chief Legal Officer</div>
    </div>
    <div class="contact">
      <p>helena.markovic@brightvale-example.com.au</p>
      <p>02 9000 0122 | 02 9000 6411</p>
      <p>Level 7, 214 Marlowe Street<br>Sydney NSW 2047, DX 318 Sydney</p>
      <p>www.brightvale-example.com.au</p>
    </div>
  </section>
</main>
</body>
</html>
```